Business Card Design

New business card design

Target Market(s)

Residential & Commercial Property Managers

Industry/Entity Type

Plumbing Services

Contact Information for Business Card

Name - Rowan Keddle, title - Director, Phone Number - 0431 286 517, email - rowan@tbk-plumbing.com.au, Company ABN - 73 215 904 386,

Font styles to use
Sans Serif

Colors
0054AA
0677BA
7BADD7
CADEEF
E8F1F8

```html
<!DOCTYPE html>
<html lang="en">
<head>
<meta charset="utf-8">
<title>TBK Plumbing Services – Business Card</title>
<link rel="stylesheet" href="https://fonts.googleapis.com/css2?family=Open+Sans:wght@300;400;600;700&display=swap">
<style>
  :root {
    --bg: #e9edf1;
    --card-white: #ffffff;
    --ink: #1f2429;
    --brand-blue: #29a6df;
    --brand-blue-deep: #1f93d0;
    --text-white: #ffffff;
    --shadow: rgba(20, 30, 40, 0.18);
  }
  * { box-sizing: border-box; margin: 0; padding: 0; }
  html, body {
    width: 1200px; height: 900px; overflow: hidden;
    background: var(--bg);
    font-family: "Open Sans", Arial, sans-serif;
  }
  .sheet {
    position: relative; width: 1200px; height: 900px;
    display: flex; flex-direction: column; align-items: center; justify-content: center; gap: 56px;
  }
  .card {
    position: relative; width: 600px; height: 328px;
    border-radius: 24px; overflow: hidden;
    box-shadow: 0 14px 34px var(--shadow);
  }

  /* Front */
  .card-front { background: var(--card-white); }
  .front-brand {
    position: absolute; top: 62px; left: 250px;
    display: flex; align-items: center; gap: 12px;
    color: var(--ink); font-weight: 400; font-size: 30px; letter-spacing: 0.5px;
  }
  .brand-dot {
    width: 16px; height: 16px; border-radius: 50%;
    background: var(--brand-blue); flex: none;
  }
  .identity-band {
    position: absolute; left: 0; top: 188px; width: 262px; height: 108px;
    background: var(--ink);
    display: flex; flex-direction: column; align-items: flex-end; justify-content: center;
    padding-right: 20px;
  }
  .person-name { color: var(--brand-blue); font-weight: 600; font-size: 27px; line-height: 1.1; }
  .person-title { color: var(--text-white); font-weight: 400; font-size: 16px; margin-top: 2px; }
  .contact-band {
    position: absolute; left: 262px; right: 0; top: 188px; height: 108px;
    background: var(--brand-blue);
    display: flex; flex-direction: column; justify-content: center;
    padding-left: 20px; gap: 3px;
    color: var(--text-white); font-size: 16px; font-weight: 400;
  }
  .contact-line { display: flex; align-items: center; gap: 8px; line-height: 1.35; }
  .contact-line svg { width: 13px; height: 13px; flex: none; }

  /* Back */
  .card-back {
    background: linear-gradient(160deg, var(--brand-blue-deep), var(--brand-blue) 60%, #2cabe3);
    display: flex; align-items: center; justify-content: center;
  }
  .back-brand {
    display: flex; align-items: center; gap: 14px;
    color: var(--text-white); font-weight: 400; font-size: 36px; letter-spacing: 0.5px;
  }
  .back-brand .brand-dot { background: var(--text-white); width: 18px; height: 18px; }
</style>
</head>
<body>
  <main class="sheet">
    <section class="card card-front" aria-label="Business card front">
      <div class="front-brand"><span class="brand-dot"></span><span>TBK Plumbing Services</span></div>

      <div class="identity-band">
        <p class="person-name">Rowan Keddle</p>
        <p class="person-title">Director</p>
      </div>

      <div class="contact-band">
        <p class="contact-line">ABN - 73 215 904 386</p>
        <p class="contact-line">
          <svg viewBox="0 0 24 24" aria-hidden="true"><path fill="#fff" d="M6.6 10.8a15.1 15.1 0 0 0 6.6 6.6l2.2-2.2a1 1 0 0 1 1-.25 11.4 11.4 0 0 0 3.6.57 1 1 0 0 1 1 1V20a1 1 0 0 1-1 1A17 17 0 0 1 3 4a1 1 0 0 1 1-1h3.5a1 1 0 0 1 1 1c0 1.25.2 2.45.57 3.57a1 1 0 0 1-.25 1z"/></svg>
          0431 286 517
        </p>
        <p class="contact-line">
          <svg viewBox="0 0 24 24" aria-hidden="true"><rect x="2" y="5" width="20" height="14" rx="2" fill="#fff"/><path d="M3 6l9 7 9-7" fill="none" stroke="#29a6df" stroke-width="2"/></svg>
          rowan@tbk-plumbing.com.au
        </p>
      </div>
    </section>

    <section class="card card-back" aria-label="Business card back">
      <div class="back-brand"><span class="brand-dot"></span><span>TBK Plumbing Services</span></div>
    </section>
  </main>
</body>
</html>
```